Website for "Bright Morrow Ltd" cleaning bsuiness

We require a website to expose our business to the local market. We want to provide background on who we are and what we do but in an easily digestible way. We clean domestic and commercial premises and want to provide a list of all of our services to potential customers. We operate out of Warrington in the UK.

We would like the website to be animated in some way so that the experience of using it is not dull or mundane. This website needs to be an extension of our company.

Target Market(s)

30 - 60 year olds for Domestic plus commercial clients

Industry/Entity Type

Cleaning Service

Coding

Coded - Design and coding required

Number of Pages Required

4 page

Font styles to use
Sans Serif

Colors
0455a3
3176b5
85acd3
cfdeed
ffffff
000000
1b1b1b
c8c8c8
757575

Requirements
Must have
• Logo which has been provided. Theme based around the logo and its colours. Simple layout to avoid confusion.
Nice to have
• Animations where possible to impress the customer.
Should not have
• any pictures of cleaning equipment, fairies, maids etc

```html
<!DOCTYPE html>
<html lang="en">
<head>
<meta charset="utf-8">
<title>Bright Morrow Ltd — Professional Cleaning Service</title>
<link href="https://fonts.googleapis.com/css2?family=Raleway:wght@300;400;600;700&family=Open+Sans:wght@400;600&family=Dancing+Script:wght@600&display=swap" rel="stylesheet">
<style>
:root{
  --blue:#0455a3;
  --blue-mid:#3176b5;
  --blue-soft:#85acd3;
  --blue-pale:#cfdeed;
  --white:#ffffff;
  --ink:#1b1b1b;
  --line:#c8c8c8;
  --grey:#757575;
}
*{margin:0;padding:0;box-sizing:border-box}
html,body{width:1200px;height:2992px;overflow:hidden;background:var(--white)}
body{position:relative;font-family:'Open Sans',sans-serif;color:var(--grey);font-size:14px;line-height:1.6}
.section{position:absolute;left:0;width:1200px}
h2{font-family:'Raleway',sans-serif;font-weight:400;text-transform:uppercase;letter-spacing:1px}
.script{font-family:'Dancing Script',cursive;font-weight:600}

/* hero */
.hero{top:0;height:660px}
.hero-photo{position:absolute;inset:0;height:620px;background:linear-gradient(180deg,#e9edf1 0%,#f6f7f9 45%,#dfe4ea 100%)}
.nav{position:absolute;top:0;left:340px;display:flex;gap:0;font-family:'Raleway',sans-serif;font-size:14px;font-weight:600;color:var(--ink);text-transform:uppercase}
.nav a{display:block;padding:18px 22px;color:var(--ink);text-decoration:none;border-top:3px solid transparent}
.nav a.active{border-top-color:var(--blue);color:var(--blue)}
.brand-hero{position:absolute;top:200px;left:0;width:1200px;text-align:center}
.brand-name{font-family:'Raleway',sans-serif;font-weight:700;color:var(--blue);font-size:78px;line-height:1;display:inline-flex;align-items:center;gap:22px}
.brand-dot{width:54px;height:54px;border-radius:50%;background:var(--blue)}
.brand-tag{margin-top:22px;font-family:'Raleway',sans-serif;font-size:26px;color:var(--blue);letter-spacing:1px}
.hero-edge{position:absolute;left:0;top:520px}

/* welcome */
.welcome{top:700px;text-align:center}
.welcome h2{font-size:40px;color:var(--ink)}
.welcome h2 span{color:var(--blue)}
.welcome p{width:820px;margin:14px auto 0;font-size:13px;line-height:1.75}
.btn{display:inline-block;background:var(--blue);color:var(--white);font-family:'Raleway',sans-serif;font-weight:600;font-size:15px;padding:12px 26px;margin-top:24px;text-transform:uppercase}

/* domestic */
.domestic{top:1032px;height:468px}
.domestic-photo{position:absolute;right:0;top:0;width:640px;height:468px;background:linear-gradient(135deg,#d7c9b4 0%,#eae3d8 50%,#c9ced6 100%)}
.domestic-panel{position:absolute;left:0;top:0}
.domestic-text{position:absolute;left:80px;top:60px;width:470px;color:var(--white)}
.domestic-text h2{font-size:38px;color:var(--white)}
.domestic-text .script{font-size:20px;margin-top:4px}
.service-list{list-style:none;margin-top:16px;font-size:14px}
.service-list li{position:relative;padding-left:22px;margin-bottom:8px}
.service-list li::before{content:"";position:absolute;left:4px;top:8px;width:7px;height:7px;border-radius:50%;background:var(--white)}
.service-list li p{font-size:12px;color:var(--blue-pale);line-height:1.5;margin-top:2px}

/* about cards */
.about{top:1540px;height:200px}
.card{position:absolute;top:0;width:500px;height:200px;background:var(--white);border:1px solid var(--line);display:flex}
.card-photo{width:200px;height:198px;background:linear-gradient(160deg,#dfe6ee,#c8d2dc)}
.card-body{padding:14px 20px}
.card-body h3{font-family:'Raleway',sans-serif;font-weight:400;font-size:26px;color:var(--ink)}
.card-body h3 span{color:var(--blue)}
.card-body p{font-size:12px;line-height:1.6;margin-top:6px}
.more{font-family:'Raleway',sans-serif;font-weight:700;font-size:13px;color:var(--blue);margin-top:8px;display:block}

/* commercial */
.commercial{top:1780px;height:400px}
.commercial-photo{position:absolute;left:0;top:0;width:700px;height:400px;background:linear-gradient(135deg,#b8a48a 0%,#d9cbb6 55%,#a89479 100%)}
.commercial-panel{position:absolute;right:0;top:0}
.commercial-text{position:absolute;right:80px;top:46px;width:470px;text-align:right;color:var(--white)}
.commercial-text h2{font-size:38px}
.commercial-text .script{font-size:20px}
.commercial-text p{font-size:12px;line-height:1.6;margin-top:10px;color:var(--blue-pale)}
.tick-list{list-style:none;margin-top:14px;font-size:14px}
.tick-list li{margin-bottom:6px}
.tick-list li::after{content:"›";margin-left:12px;font-weight:700}

/* testimonial */
.testimonial{top:2240px;height:320px;text-align:center}
.testimonial h2{font-size:40px;color:var(--ink)}
.avatar{width:110px;height:110px;border-radius:50%;margin:24px auto 0;background:linear-gradient(135deg,#efe4da,#d9c9ba);border:4px solid var(--blue-pale)}
.testimonial p{width:860px;margin:20px auto 0;font-size:13px}
.client{font-family:'Raleway',sans-serif;font-weight:700;font-size:14px;color:var(--blue);margin-top:12px;display:block}
.arrow{position:absolute;top:100px;width:40px;height:40px;border-radius:50%;border:1px solid var(--line);display:flex;align-items:center;justify-content:center}

/* footer */
.footer{top:2592px;height:400px}
.footer-bg{position:absolute;left:0;top:0}
.footer-cols{position:absolute;top:110px;left:80px;display:flex;gap:0;width:1040px}
.col{width:260px}
.footer-brand .brand-name{font-size:34px;gap:10px}
.footer-brand .brand-dot{width:26px;height:26px}
.footer-brand .brand-tag{font-size:14px;margin-top:8px}
.col h4{font-family:'Raleway',sans-serif;font-weight:700;font-size:16px;color:var(--blue);text-transform:uppercase;margin-bottom:14px}
.links{list-style:none;font-size:13px;color:var(--ink)}
.links li{padding-left:16px;position:relative;margin-bottom:3px}
.links li::before{content:"›";position:absolute;left:0;color:var(--blue);font-weight:700}
.contact{font-size:12px;color:var(--ink)}
.contact div{display:flex;gap:10px;margin-bottom:12px;align-items:flex-start}
.contact svg{flex:none;margin-top:2px}
.news p{font-size:12px;color:var(--ink);line-height:1.5}
.news .field{margin-top:12px;width:200px;height:30px;border:1px solid var(--line);background:var(--white);font-size:12px;padding:5px 8px;color:var(--grey)}
.news .btn{margin-top:10px;padding:6px 24px;font-size:13px}
.copyright{position:absolute;left:0;bottom:0;width:1200px;height:32px;background:var(--blue);color:var(--white);font-size:12px;text-align:center;line-height:32px}
</style>
</head>
<body>

<header class="section hero">
  <div class="hero-photo" role="img" aria-label="Bright, white living room interior with large windows"></div>
  <nav class="nav">
    <a class="active">Home</a><a>About Us</a><a>Services</a><a>Blog</a><a>Contact Us</a>
  </nav>
  <div class="brand-hero">
    <div class="brand-name"><span class="brand-dot"></span>Bright Morrow Ltd</div>
    <div class="brand-tag">Professional Cleaning Service</div>
  </div>
  <svg class="hero-edge" width="1200" height="140" viewBox="0 0 1200 140">
    <path d="M0 80 Q600 20 1200 80 L1200 140 L0 140 Z" fill="#ffffff"/>
    <path d="M0 80 Q600 20 1200 80" fill="none" stroke="#0455a3" stroke-width="5"/>
  </svg>
</header>

<section class="section welcome">
  <h2>Welcome to <span>Bright Morrow</span></h2>
  <p>Lorem ipsum is simply dummy text of the printing and typesetting industry. Lorem ipsum has been the standard dummy text ever since the 1500s, when an unknown printer took a galley of type and scrambled it to make a type specimen book for many years.</p>
  <p>Lorem ipsum is simply dummy text of the printing and typesetting industry. Lorem ipsum has been the industry standard dummy text ever since the 1500s, when an unknown printer took a galley of type to make a specimen book.</p>
  <span class="btn">Know More</span>
</section>

<section class="section domestic">
  <div class="domestic-photo" role="img" aria-label="Folded fresh laundry beside a steam iron"></div>
  <svg class="domestic-panel" width="700" height="468" viewBox="0 0 700 468">
    <polygon points="0,0 700,0 560,468 0,468" fill="#0455a3"/>
  </svg>
  <div class="domestic-text">
    <h2>Domestic Services :</h2>
    <div class="script">Weekly, fortnightly, monthly and either cleans available</div>
    <ul class="service-list">
      <li>Ironing<p>Lorem ipsum is simply dummy text of the printing and typesetting industry. Lorem ipsum has been the industry standard.</p></li>
      <li>Carpet Cleaning</li>
      <li>Tiled floor steam clean</li>
      <li>End of tenancy clean</li>
      <li>New house pre-moving in clean</li>
      <li>Emergency requested clean</li>
    </ul>
  </div>
</section>

<section class="section about">
  <article class="card" style="left:80px">
    <div class="card-photo" role="img" aria-label="Team member at work in a tidy kitchen"></div>
    <div class="card-body">
      <h3>Who <span>We Are ?</span></h3>
      <p>Lorem ipsum is simply dummy text of the printing and typesetting industry. Lorem ipsum has been the industry standard dummy text ever since the early days.</p>
      <span class="more">READ MORE...</span>
    </div>
  </article>
  <article class="card" style="left:620px">
    <div class="card-photo" role="img" aria-label="Clean and bright living room"></div>
    <div class="card-body">
      <h3>What <span>We Do ?</span></h3>
      <p>Lorem ipsum is simply dummy text of the printing and typesetting industry. Lorem ipsum has been the industry standard dummy text ever since the early days.</p>
      <span class="more">READ MORE...</span>
    </div>
  </article>
</section>

<section class="section commercial">
  <div class="commercial-photo" role="img" aria-label="Tiled floor being deep cleaned"></div>
  <svg class="commercial-panel" width="700" height="400" viewBox="0 0 700 400">
    <polygon points="160,0 700,0 700,400 0,400" fill="#0455a3"/>
  </svg>
  <div class="commercial-text">
    <h2>Commercial Cleaning</h2>
    <div class="script">contract daily cleaning</div>
    <p>Lorem ipsum is simply dummy text of the printing and typesetting industry. Lorem ipsum has been the industry standard dummy text.</p>
    <ul class="tick-list">
      <li>Vacuuming</li>
      <li>Desk polishing</li>
      <li>Bin emptying</li>
      <li>Toilet cleaning</li>
    </ul>
  </div>
</section>

<section class="section testimonial">
  <h2>What our client say</h2>
  <div class="avatar" role="img" aria-label="Client portrait"></div>
  <p>Lorem ipsum is simply dummy text of the printing and typesetting industry. Lorem ipsum has been the industry standard dummy text ever since the 1500s, when an unknown printer took a galley of type and scrambled it to make a type specimen book.</p>
  <span class="client">- CLIENT NAME</span>
  <div class="arrow" style="left:80px"><svg width="12" height="12" viewBox="0 0 12 12"><path d="M8 1 L3 6 L8 11" fill="none" stroke="#757575" stroke-width="2"/></svg></div>
  <div class="arrow" style="right:80px"><svg width="12" height="12" viewBox="0 0 12 12"><path d="M4 1 L9 6 L4 11" fill="none" stroke="#757575" stroke-width="2"/></svg></div>
</section>

<footer class="section footer">
  <svg class="footer-bg" width="1200" height="400" viewBox="0 0 1200 400">
    <defs><linearGradient id="fbg" x1="0" y1="0" x2="0" y2="1"><stop offset="0" stop-color="#cfdeed"/><stop offset="1" stop-color="#f4f7fb"/></linearGradient></defs>
    <path d="M0 70 Q600 0 1200 70 L1200 400 L0 400 Z" fill="url(#fbg)"/>
    <path d="M0 70 Q600 0 1200 70" fill="none" stroke="#0455a3" stroke-width="5"/>
  </svg>
  <div class="footer-cols">
    <div class="col footer-brand">
      <div class="brand-name"><span class="brand-dot"></span>Bright Morrow</div>
      <div class="brand-tag">Professional Cleaning Service</div>
    </div>
    <div class="col">
      <h4>Usefull Links</h4>
      <ul class="links"><li>Home</li><li>About Us</li><li>Services</li><li>Blog</li><li>Contact Us</li></ul>
    </div>
    <div class="col">
      <h4>Get in Touch</h4>
      <div class="contact">
        <div><svg width="14" height="16" viewBox="0 0 14 16"><path d="M7 1a5 5 0 0 1 5 5c0 4-5 9-5 9S2 10 2 6a5 5 0 0 1 5-5z" fill="#0455a3"/><circle cx="7" cy="6" r="2" fill="#fff"/></svg><span>12 Lorem Lane, simply dummy text, Warrington</span></div>
        <div><svg width="14" height="14" viewBox="0 0 14 14"><path d="M3 1l2 3-1.5 1.5a8 8 0 0 0 5 5L10 9l3 2-1 2c-6 0-11-5-11-11z" fill="#0455a3"/></svg><span>01925 000 123</span></div>
        <div><svg width="14" height="12" viewBox="0 0 14 12"><rect x="0.5" y="0.5" width="13" height="11" fill="none" stroke="#0455a3"/><path d="M1 1l6 5 6-5" fill="none" stroke="#0455a3"/></svg><span>hello@brightmorrow.example</span></div>
      </div>
    </div>
    <div class="col news">
      <h4>Newsletter</h4>
      <p>Would you like to receive exclusive access to articles, offers and our regular monthly newsletter?</p>
      <div class="field">Enter Email</div>
      <span class="btn">Submit</span>
    </div>
  </div>
  <div class="copyright">© 2016 Bright Morrow Ltd - All rights reserved</div>
</footer>

</body>
</html>
```